Landing page for Quorvath Computer Support

We need a high converting landing page for PPC campaign for Quorvath Computer Support. We are looking for a responsive page which works for PC, VELTRIX and Mobile devices. Main purpose of page will be to generate calls to our Toll free number. Users can also opt for chat with technician to resolve their issues but only CTA of page should be to generate call to our toll free number.
Current landing page we use is- https://brivandohelp.example/quorvath-computer-support.html (called Link1 in text below)
We will need following in new landing page:
1. Disclaimer - This is legally mandatory near CTA
PelmoraAssist is an independent provider of technical support services for several third party brands. If your product is under warranty or not repair service maybe available at brand owner or official website. Use of names, trademarks is for reference only. We disclaim any ownership, right, affiliation or endorsement of or by any such third party products or brands.
2. New Image of Customer Service Rep. See Link1
3. Description/details of what support for Quorvath we provide. See Link1. You can take some or all content from link1
4. Testimonials
5. Chat option
6. Footer with following- Contact Info and copyright statement. See Link1
7. You can place trust building logo like Zintrel Secure and Halcorix to your choice to increase effectiveness of landing page
Take ideas from http://plovique.example/landing-page-articles/the-anatomy-of-a-landing-page/. We can put whatever is necessary on new landing page to reach goal of high conversions.
Landing pages designs we like:
http://www.setup-shieldkit.example/5920147/zintrel/zintrel-support.html
http://www.mendbayo.example/quorvath/quorvath_support/quorvath_help_support.php
http://fluxdorin.example/fix-computer/
New Details:
-----------------
I generally prefer white background for landing pages. You can also use grey and any other color which goes with it. In the end, goal is high conversion rate.
Updates
Since some of the designs posted have ability to collect email address, I would like to clarify that Only CTA is to call toll free number. We don't need to collect email addresses. Reason is 99.9% of customers will only reach out to us if they have an urgent and immediate problem to resolve. They will call toll free and get support via remote connection but won't send email. Very few will opt to chat with technician. Even if they send email, they will never buy our services because they would have contacted somebody else to solve their immediate problem via remote connection.
Thanks
Home users and small business

```html
<!DOCTYPE html>
<html lang="en">
<head>
<meta charset="utf-8">
<title>Quorvath Computer Support</title>
<link href="https://fonts.googleapis.com/css2?family=Roboto:wght@400;500;700&family=Ubuntu:wght@400;500&display=swap" rel="stylesheet">
<style>
:root{
  --bg:#e6e6e6;
  --page:#ffffff;
  --blue:#2b86c0;
  --blue-dark:#2272a6;
  --ink:#333333;
  --muted:#777777;
  --card:#e9ebee;
  --field:#e8e9ea;
}
*{box-sizing:border-box;margin:0;padding:0}
html,body{width:686px;height:1200px;overflow:hidden;background:var(--bg)}
body{position:relative;font-family:'Roboto',sans-serif;color:var(--ink)}
.page{position:absolute;left:57px;top:19px;width:573px;height:1154px;background:var(--page);border-top:2px solid var(--blue)}
.abs{position:absolute}

.brand{left:9px;top:20px;display:flex;align-items:center;gap:5px}
.brand-dot{width:16px;height:16px;border-radius:50%;background:#8a8f95}
.brand-name{font-size:18px;font-weight:500;color:#2b2f33;letter-spacing:-.3px}
.callbox{right:14px;top:15px;text-align:right}
.callbox .lbl{color:var(--blue);font-size:12px;margin-right:24px}
.callbox .num{font-size:12px;color:#333;margin-right:24px}
.callbox svg{position:absolute;right:0;top:8px}

.nav{left:9px;top:58px;width:555px;height:30px;background:var(--blue);display:flex}
.nav a{color:#fff;font-size:8.5px;font-weight:500;text-decoration:none;display:flex;align-items:center;justify-content:center;height:100%}
.nav a.active{background:#111}

.hero{left:9px;top:88px;width:555px;height:259px;
  background:
    radial-gradient(ellipse 120px 150px at 455px 110px,#e9c9b4 0%,rgba(233,201,180,.55) 45%,rgba(233,201,180,0) 80%),
    radial-gradient(ellipse 90px 130px at 500px 70px,#4a3428 0%,rgba(74,52,40,0) 75%),
    radial-gradient(ellipse 110px 90px at 330px 180px,rgba(205,180,160,.7),rgba(205,180,160,0) 80%),
    linear-gradient(90deg,#eef2f6 0%,#e2e9ef 40%,#d3dde6 100%)}
.hero-t1{left:65px;top:172px;font-size:19px;font-weight:500;color:#222;text-shadow:1px 1px 1px rgba(0,0,0,.15)}
.hero-t1 span{font-size:13px;color:var(--blue);font-weight:400;margin-right:5px}
.hero-t2{left:65px;top:200px;font-size:20px;font-weight:500;color:#222;text-shadow:1px 1px 1px rgba(0,0,0,.15)}
.btn{background:var(--blue);color:#fff;font-size:8px;display:flex;align-items:center;justify-content:center}
.hero-btn{left:68px;top:238px;width:66px;height:18px;box-shadow:2px 2px 2px rgba(0,0,0,.25)}
.hero-arrow{left:22px;top:225px}
.dots{left:275px;top:353px;display:flex;gap:3px}
.dots i{width:4px;height:4px;border-radius:50%;background:#ccc}
.dots i:first-child{background:var(--blue)}

.quick{left:347px;top:278px;width:204px;height:214px;background:#fff;box-shadow:0 1px 4px rgba(0,0,0,.2)}
.quick h3{background:var(--blue);color:#fff;font-weight:400;font-size:13px;text-align:center;height:31px;line-height:31px}
.quick p{font-size:6.5px;line-height:1.4;color:#444;text-align:justify;margin:9px 10px 0}
.field{background:var(--field);color:#999;font-size:7.5px;display:flex;align-items:center;padding-left:7px;height:19px}
.f-name{left:10px;top:116px;width:184px}
.f-svc{left:10px;top:145px;width:184px}
.f-svc b{position:absolute;right:0;top:0;width:18px;height:19px;background:var(--blue)}
.cta{left:10px;top:179px;width:184px;height:19px;box-shadow:0 2px 0 var(--blue-dark)}

.intro{left:8px;top:369px;width:323px}
.intro h2{font-size:13px;font-weight:400;color:var(--blue)}
.intro .sub{font-size:9.5px;margin-top:3px}
.intro p{font-size:6.6px;line-height:1.55;color:#666;text-align:justify;margin-top:8px}
.more{left:242px;top:474px;width:86px;height:17px;font-size:7px}

.t-title{left:0;width:573px;top:520px;text-align:center;font-size:13px;font-weight:400;color:var(--blue)}
.tcard{top:550px;width:176px;height:74px;background:var(--card)}
.tcard .av{position:absolute;left:10px;top:7px;width:17px;height:17px;border-radius:50%;background:#c9cfd4;border:2px solid #fff}
.tcard p{position:absolute;left:10px;top:34px;right:8px;font-size:6.6px;line-height:1.5;color:#8a8d90;font-style:italic}
.tname{top:641px;font-size:6.4px;color:#888}
.tname b{color:var(--blue);font-weight:500}

.promo{top:681px;width:178px;height:96px;box-shadow:0 3px 4px rgba(0,0,0,.15)}
.p1{left:9px;background:radial-gradient(ellipse 50px 45px at 140px 40px,#e7c3ac,rgba(231,195,172,0) 80%),linear-gradient(90deg,#dfe6ec,#b9a496)}
.p2{left:197px;background:radial-gradient(ellipse 55px 30px at 85px 55px,#8ab4c8,rgba(138,180,200,0) 80%),linear-gradient(180deg,#f1ead8 80%,#6f6a66 80%)}
.p3{left:385px;background:radial-gradient(ellipse 60px 30px at 120px 35px,#3f9ed3,rgba(63,158,211,0) 85%),linear-gradient(135deg,#e6e9ec,#c4cdd4)}
.chat{left:4px;top:62px;width:100px;height:25px;border-radius:13px;background:var(--blue);border:2px solid #fff;color:#fff;font-weight:700;font-size:11.5px;display:flex;align-items:center;justify-content:center;letter-spacing:.3px}

.footer{left:9px;top:811px;width:555px;height:306px;background:var(--blue);font-family:'Ubuntu',sans-serif;color:#fff}
.footer h4{position:absolute;font-weight:400;font-size:10.5px}
.footer ul{position:absolute;list-style:none;font-size:6.9px;line-height:10.35px}
.footer li:before{content:"";display:inline-block;width:2.5px;height:2.5px;border-radius:50%;background:#fff;margin-right:7px;vertical-align:middle}
.contact{position:absolute;left:320px;top:200px;font-size:6.9px;line-height:10.4px}
.badge{position:absolute;background:#fff;border-radius:2px}
.bottom{left:9px;top:1117px;width:555px;height:29px;background:var(--blue-dark);color:#fff;font-family:'Ubuntu',sans-serif;font-size:6.9px}
.bottom span{position:absolute;left:19px;top:11px}
.social{position:absolute;right:14px;top:10px;display:flex;gap:16px}
.social i{width:9px;height:9px;border-radius:50%;background:#fff}
</style>
</head>
<body>
<div class="page">
  <div class="abs brand"><span class="brand-dot"></span><span class="brand-name">BrivandoHelp</span></div>
  <div class="abs callbox">
    <div class="lbl">Call Now</div>
    <div class="num">1-800-555-0147</div>
    <svg width="19" height="19" viewBox="0 0 20 20"><circle cx="10" cy="10" r="8.5" fill="none" stroke="#2b86c0" stroke-width="1.5"/><path d="M7 5.5l2 2.2-1 1.2c.6 1.3 1.6 2.3 2.9 2.9l1.2-1 2.2 2-1.2 1.5C9.9 14.2 5.8 10.1 5.6 6.9z" fill="#2b86c0"/></svg>
  </div>

  <nav class="abs nav">
    <a class="active" style="width:76px">Home</a>
    <a style="width:78px">About Us</a>
    <a style="width:66px">Service</a>
    <a style="width:80px">Testimonials</a>
    <a style="width:71px">Support</a>
    <a style="width:70px">Contact Us</a>
  </nav>

  <div class="abs hero" role="img" aria-label="Smiling customer service representative wearing a headset, with colleagues in a bright call centre behind her"></div>
  <div class="abs hero-t1"><span>24x7</span>Tech Support</div>
  <div class="abs hero-t2">For Quorvath Computer</div>
  <div class="abs btn hero-btn">Read More</div>
  <svg class="abs hero-arrow" width="19" height="19" viewBox="0 0 20 20"><circle cx="10" cy="10" r="10" fill="#9a9a9a"/><path d="M11.5 5.5L7 10l4.5 4.5" fill="none" stroke="#fff" stroke-width="2"/></svg>
  <div class="abs dots"><i></i><i></i><i></i></div>

  <section class="abs intro">
    <h2>Support for Quorvath Computer</h2>
    <div class="sub">Call at 1-800-555-0147 for instant support.</div>
    <p>When you face a computer problem, identifying the problem and properly fixing it consumes precious time, labor, and resources. We are here to streamline the tech support process, offering high-quality, professional tech support for Quorvath computers. All of our technicians are fully certified and trained, with experience and expertise dealing specifically with Quorvath computers. Our technicians can efficiently deal with a range of problems and issues, including:</p>
  </section>
  <div class="abs btn more">READ MORE</div>

  <section class="abs quick">
    <h3>QUICK CONTACT</h3>
    <p>PelmoraAssist is an independent provider of technical support services for several third party brands. If your product is under warranty or not repair service maybe available at brand owner or official website. Use of names, trademarks is for reference only. We disclaim any ownership, right, affiliation or endorsement of or by any such third party products or brands.</p>
    <div class="abs field f-name">Name</div>
    <div class="abs field f-svc">Service For<b><svg width="18" height="19" viewBox="0 0 18 19"><path d="M6 8l3 3 3-3z" fill="#fff"/></svg></b></div>
    <div class="abs btn cta">CALL TO ACTION</div>
  </section>

  <h2 class="abs t-title">Client Testimonials</h2>
  <div class="abs tcard" style="left:7px"><span class="av"></span><p>"Aenean feugiat blandit velit, posuere icon-dimentum felis dapibus id. Cum sociis na-toque penatibus etion tint coloreo"</p></div>
  <div class="abs tcard" style="left:197px"><span class="av"></span><p>"Praesent ullamcorper nulla ultrices nibh rutrum, sed dapibus augue ornare esque convallis massa in elit cursus "</p></div>
  <div class="abs tcard" style="left:388px"><span class="av"></span><p>"Duis ligula purus, molestie nec iaculis et, cursus vel risus. Sed est magna, ultricies sit amet elit et, ullamcorper susc"</p></div>
  <div class="abs tname" style="left:7px"><b>-Jon Tarrow</b> / Company Name</div>
  <div class="abs tname" style="left:199px"><b>- Amara Tillen</b> / Company Name</div>
  <div class="abs tname" style="left:390px"><b>- Pell Doran</b> / Company Name</div>

  <div class="abs promo p1" role="img" aria-label="Support agent with headset offering live chat"><div class="abs chat">CHAT NOW</div></div>
  <div class="abs promo p2" role="img" aria-label="Illustrated desk with lamp and screens welcoming visitors to the new blog"></div>
  <div class="abs promo p3" role="img" aria-label="Close-up of a keyboard with a blue news key"></div>

  <footer class="abs footer">
    <h4 style="left:16px;top:17px">Support</h4>
    <ul style="left:17px;top:37px">
      <li>Support for Slow PC</li><li>Support for Computer Issues</li><li>Support for PC Optimization</li><li>Support for PC Tuneup</li><li>Support for Veltrix</li><li>Support for Arvena</li><li>Support for Glint Player</li><li>Support for Registry</li><li>Support for Corvel Browser</li><li>Support for Ostara</li><li>Support for Savenne</li><li>Support for Delmor Computer</li><li>Support for Hexpra Computer</li><li>Support Tosevin Computer</li><li>Support For Acrilo Computer</li><li>Support For Quorvath Computer</li><li>Support for Sorelan Computer</li><li>Support For Compria Computer</li><li>Support for Linvara Router</li><li>Support for Belroth Router</li><li>Support for Ciswane Router</li><li>Support for Netholm Router</li><li>Support for Pomba Games</li>
    </ul>
    <ul style="left:161px;top:37px">
      <li>Support for Dravlink Router</li><li>Support for Asoren Router</li><li>Support for Zintrel Antivirus</li><li>Support for Kasmiro Antivirus</li><li>Support for Avelin Antivirus</li><li>Support for Avrix Antivirus</li><li>Support for Avosta Antivirus</li><li>Support for Nortavi AntiVirus</li><li>Support for Bytehelm Antivirus</li><li>Support for Webmorra Antivirus</li><li>Support for Vantrel Antivirus</li><li>Support for Trelmic Antivirus</li><li>Support for Tolvane Defense Antivirus</li><li>Support for Pandril Antivirus</li><li>Support for Printers</li><li>Support for Delmor Printer</li><li>Support for Hexpra Printer</li><li>Support for Brevik Printer</li><li>Support for Panvesta Printer</li><li>Support for Epsira Printer</li><li>Support for Carmello Printer</li><li>Support for Samvoro Printer</li>
    </ul>
    <h4 style="left:320px;top:17px">Plan</h4>
    <ul style="left:321px;top:37px"><li>Silver Plan</li><li>Gold Plan</li><li>Platinum Plan</li></ul>
    <h4 style="left:320px;top:80px">Quick Links</h4>
    <ul style="left:321px;top:100px"><li>About Us</li><li>Contact Us</li><li>Terms &amp; Conditions</li><li>Privacy Policy</li><li>Refund Policy</li><li>Disclaimer</li></ul>
    <h4 style="left:320px;top:180px">Contact Info</h4>
    <div class="contact">18 Linden St, Marrowfield, NY, 10000, USA.<br>Ph: 1-800-555-0147<br>Fax: 212-555-0188<br>Email: support@brivandohelp.example</div>

    <div class="badge" style="left:467px;top:22px;width:69px;height:34px"></div>
    <div class="badge" style="left:467px;top:64px;width:69px;height:19px"></div>
    <div class="badge" style="left:467px;top:91px;width:69px;height:30px"></div>
    <div class="badge" style="left:467px;top:129px;width:72px;height:11px"></div>
    <div style="position:absolute;left:486px;top:155px;width:34px;height:34px;border-radius:50%;background:#e8b93a"></div>
  </footer>
  <div class="abs bottom"><span>© 2014 BrivandoHelp - All Rights Reserved.</span><div class="social"><i></i><i></i><i></i><i></i></div></div>
</div>
</body>
</html>
```